New web design for a service provider in the medical field

We are looking for a new design for our website. We are a company that repairs and sells medical endoscopes. Our customers include doctors and hospitals. Our current website can be found at https://lumavex.de/en/lumavex-english.
We need a new web design (without programming) for the following 3 pages:
-Startpage https://lumavex.de/en/lumavex-english/
-Used endoscopes https://lumavex.de/en/used-endoscopes/
-Purchase https://lumavex.de/en/purchase/
The design should be modern and stylish.
The blue color of the logo should be reflected on the page, but not too intrusive.
I have uploaded the images from the header. If more images are needed, let me know and I will upload them.

Target Market(s)
Doctors and hospitals

```html
<!DOCTYPE html>
<html lang="en">
<head>
<meta charset="utf-8">
<title>Lumavex – Endoscope Repair &amp; Sales</title>
<link href="https://fonts.googleapis.com/css2?family=Rubik:wght@300;400;500;700&display=swap" rel="stylesheet">
<style>
:root{
  --blue:#0aa1e2;
  --blue-deep:#0b8fd0;
  --navy:#163a5a;
  --heading:#1c4a6b;
  --text:#5d6a74;
  --ink:#243544;
  --pale:#eaf6fb;
  --footer:#151a42;
  --orange:#ff9a0a;
  --white:#fff;
}
*{box-sizing:border-box;margin:0;padding:0}
html,body{width:1200px;height:4815px;overflow:hidden}
body{font-family:"Rubik",sans-serif;color:var(--text);background:var(--white);position:relative}
.abs{position:absolute}
a{color:inherit;text-decoration:none}

/* top bar */
.topbar{top:0;left:0;width:1200px;height:38px;background:#f4fafd;font-size:11px;color:var(--ink)}
.topbar .tagline{left:99px;top:12px}
.topbar .socials{left:860px;top:12px;display:flex;gap:26px}
.dot-icon{width:10px;height:10px;border-radius:50%;background:var(--blue)}
.topbar .lang{left:1028px;top:11px;display:flex;gap:6px;align-items:center}
.lang .flag{width:14px;height:14px;border-radius:50%;background:#c8202f}

/* header */
.header{top:38px;left:0;width:1200px;height:130px;background:var(--white)}
.brand{display:flex;align-items:center;gap:8px;font-weight:500;font-size:22px;color:var(--navy)}
.brand .mark{width:14px;height:14px;border-radius:50%;background:var(--blue)}
.header .brand{left:110px;top:36px}
.mainnav{left:374px;top:44px;display:flex;gap:42px;font-size:10px;color:var(--ink);letter-spacing:.3px}
.contact-chip{display:flex;gap:12px;align-items:center}
.chip-icon{width:38px;height:38px;border-radius:50%;border:1.5px solid var(--blue);display:flex;align-items:center;justify-content:center}
.chip-label{font-size:9px;letter-spacing:1.5px;font-weight:500;color:var(--ink)}
.chip-value{font-size:13px;color:var(--ink)}
.header .email{left:696px;top:30px}
.header .phone{left:916px;top:30px}

.catnav{top:136px;left:99px;width:1002px;height:66px;background:var(--blue);z-index:3;display:flex}
.catnav ul{list-style:none;display:flex;gap:34px;align-items:center;padding-left:24px;font-size:10px;font-weight:500;color:var(--white);flex:1}
.catnav .cta{width:155px;background:var(--navy);color:var(--white);font-weight:500;font-size:15px;display:flex;align-items:center;justify-content:center}

/* hero */
.hero{top:168px;left:0;width:1200px;height:711px;background:linear-gradient(100deg,#3a4d73 0%,#56698e 55%,#7c8dab 100%)}
.hero .eyebrow{left:99px;top:168px;font-size:13px;letter-spacing:3px;color:#e3e9f2}
.hero h1{left:95px;top:206px;font-size:62px;line-height:72px;font-weight:500;color:var(--white)}
.hero p{left:97px;top:362px;width:540px;font-size:12.5px;line-height:25px;color:#eef2f8}
.btn{display:flex;align-items:center;justify-content:center;font-weight:500;font-size:14px}
.btn-blue{background:var(--blue);color:var(--white)}
.hero .btn{left:99px;top:486px;width:189px;height:66px}
.hero .arrows{left:99px;top:623px;display:flex;gap:10px}
.arrow{width:36px;height:36px;border-radius:50%;border:1.5px solid rgba(255,255,255,.7);display:flex;align-items:center;justify-content:center}
.hero .dots{left:1090px;top:332px;display:flex;flex-direction:column;gap:10px}
.hero .dots span{width:10px;height:10px;border-radius:50%;border:2px solid #fff;opacity:.6}
.hero .dots span:first-child{background:#fff;opacity:1}

/* about */
.about{top:879px;left:0;width:1200px;height:785px;background:var(--pale)}
.photo{background:linear-gradient(135deg,#e8eaee,#b7bec8);box-shadow:0 10px 30px rgba(0,0,0,.12)}
.about .photo-main{left:99px;top:103px;width:428px;height:476px;background:linear-gradient(135deg,#f1f1f3,#c9cdd3 60%,#44474c)}
.about .photo-small{left:30px;top:441px;width:308px;height:243px;border:4px solid #fff;background:linear-gradient(135deg,#f3f4f6,#c6c9ce)}
.about .badge{left:474px;top:550px;width:96px;height:96px;border-radius:50%;background:#fff;box-shadow:0 6px 20px rgba(0,0,0,.12);display:flex;align-items:center;justify-content:center}
.about h2{left:613px;top:120px;width:510px;font-size:25px;line-height:31px;font-weight:700;color:var(--heading)}
.about .copy{left:613px;top:257px;width:490px;font-size:11.5px;line-height:21px}
.about .copy p+p{margin-top:16px}
.checks{left:613px;top:442px;list-style:none;font-size:12.5px;font-weight:500;color:var(--ink)}
.checks li{display:flex;gap:16px;align-items:center;height:34px}
.checks .tick{width:14px;height:14px;border-radius:50%;background:var(--blue);display:flex;align-items:center;justify-content:center}
.about .btn{left:613px;top:632px;width:170px;height:65px}

/* brands */
.brands{top:1664px;left:0;width:1200px;height:142px;background:#f3fafd}
.brand-name{top:50px;font-size:34px;font-weight:700;letter-spacing:1px;color:var(--navy);transform:translateX(-50%)}

/* services */
.services{top:1806px;left:0;width:1200px;height:845px}
.eyebrow-dark{font-size:12px;letter-spacing:3px;color:var(--text);text-align:center;width:1200px;left:0}
.services .eyebrow-dark{top:69px}
.services h2{top:93px;left:0;width:1200px;text-align:center;font-size:40px;font-weight:700;color:var(--ink)}
.card{top:183px;width:316px;height:563px;background:#fff;box-shadow:0 6px 24px rgba(20,40,70,.08)}
.card .pic{width:316px;height:240px}
.card h3{position:absolute;left:17px;top:283px;font-size:25px;line-height:30px;font-weight:500;color:var(--heading)}
.card p{position:absolute;left:17px;top:362px;width:282px;font-size:11px;line-height:20.5px}
.card .btn{position:absolute;left:17px;top:488px;width:282px;height:57px;font-size:14px}

/* faulty band */
.faulty{top:2651px;left:0;width:1200px;height:343px;background:linear-gradient(100deg,#52637f,#6d7d98 60%,#8696ae)}
.trust{top:2723px;left:99px;width:488px;height:300px;background:var(--blue);z-index:2}
.trust .ring{position:absolute;left:62px;top:42px}
.trust p{position:absolute;left:62px;top:146px;font-size:31px;line-height:38px;color:#fff}
.faulty-text{left:660px;top:2710px;color:#fff}
.faulty-text h2{font-size:40px;line-height:50px;font-weight:500}
.faulty-text p{font-size:24px;margin-top:12px;font-weight:300}
.btn-orange{left:662px;top:2890px;width:282px;height:56px;background:var(--orange);color:#fff;font-size:14px}

/* decision */
.decision{top:2994px;left:0;width:1200px;height:884px;background:#fff}
.decision h2{top:132px;left:0;width:1234px;text-align:center;font-size:31px;line-height:34px;font-weight:500;color:var(--ink)}
.feature{width:260px;text-align:center;transform:translateX(-50%)}
.feature svg{display:block;margin:0 auto 14px}
.feature h4{font-size:14px;font-weight:500;color:var(--heading)}
.feature p{font-size:11.5px;line-height:22px;margin-top:4px}
.decision .btn{left:523px;top:753px;width:184px;height:54px}

/* cta */
.cta-band{top:3878px;left:0;width:1200px;height:436px;background:linear-gradient(135deg,#0a9ae0,#13b0ee)}
.cta-band .label{top:107px;left:0;width:1200px;text-align:center;font-size:12px;letter-spacing:3px;color:#e4f4fc}
.cta-band h2{top:122px;left:0;width:1200px;text-align:center;font-size:52px;font-weight:500;color:#fff}
.cta-band .sub{top:182px;left:0;width:1200px;text-align:center;font-size:41px;font-weight:300;color:#fff}
.cta-band .btn{left:505px;top:267px;width:190px;height:66px;background:#fff;color:var(--ink)}

/* footer */
.footer{top:4314px;left:0;width:1200px;height:501px;background:var(--footer);color:#d6daeb}
.footer .brand{left:112px;top:180px;color:#fff}
.footer h5{font-size:20px;font-weight:400;color:#fff}
.footer ul{list-style:none;font-size:12px;letter-spacing:.4px}
.footer li{height:34px}
.footer .col-about{left:357px;top:98px}
.footer .col-explore{left:607px;top:96px}
.footer .col-about ul,.footer .col-explore ul{margin-top:18px}
.footer .chip-icon{border-color:var(--blue)}
.footer .chip-label,.footer .chip-value{color:#fff}
.footer .f-email{left:854px;top:100px}
.footer .f-phone{left:854px;top:172px}
.footer .f-social{left:862px;top:266px;display:flex;gap:34px}
.footer .f-social .dot-icon{background:#d6daeb}
.footer .rule{left:99px;top:400px;width:1002px;height:1px;background:rgba(255,255,255,.15)}
.footer .copy{left:0;top:440px;width:1200px;text-align:center;font-size:12px}
</style>
</head>
<body>

<div class="abs topbar">
  <span class="abs tagline">Cause the outcome matters</span>
  <div class="abs socials"><span class="dot-icon"></span><span class="dot-icon"></span><span class="dot-icon"></span><span class="dot-icon"></span></div>
  <div class="abs lang"><span class="flag"></span>English &gt;</div>
</div>

<header class="abs header">
  <div class="abs brand"><span class="mark"></span>Lumavex</div>
  <nav class="abs mainnav"><a href="#">PICK-UP ORDER</a><a href="#">ABOUT US</a><a href="#">CONTACT US</a></nav>
  <div class="abs contact-chip email">
    <span class="chip-icon"><svg width="18" height="14" viewBox="0 0 18 14" fill="none" stroke="#0aa1e2" stroke-width="1.5"><rect x="1" y="1" width="16" height="12" rx="1"/><path d="M1 2l8 6 8-6"/></svg></span>
    <div><div class="chip-label">EMAIL</div><div class="chip-value">info@lumavex.de</div></div>
  </div>
  <div class="abs contact-chip phone">
    <span class="chip-icon"><svg width="16" height="16" viewBox="0 0 24 24" fill="none" stroke="#0aa1e2" stroke-width="1.8"><path d="M5 3h4l2 5-2.5 1.5a11 11 0 006 6L16 13l5 2v4a2 2 0 01-2 2A16 16 0 013 5a2 2 0 012-2z"/></svg></span>
    <div><div class="chip-label">PHONE</div><div class="chip-value">+49 4151 555 720-0</div></div>
  </div>
</header>

<nav class="abs catnav">
  <ul><li>ENDOSCOPE REPAIR</li><li>USED ENDOSCOPES</li><li>ENDOSCOPY SYSTEMS</li><li>ENDOSCOPY ACCESSORIES</li><li>ACCESSORIES CATALOG</li><li>PURCHASE</li></ul>
  <a class="cta" href="#">Contact Now</a>
</nav>

<section class="abs hero" role="img" aria-label="Close-up of a flexible endoscope control head under a blue tint">
  <div class="abs eyebrow">YOUR FUTURE · OUR SERVICE</div>
  <h1 class="abs">Put Your Endoscope<br>in Relaible Hands !</h1>
  <p class="abs">Lumavex GmbH is specialised in the repair and sale of Olvarin, Pentrel and Fujaris flexible medical endoscopes. As a service-oriented company, we are at your side with our knowledge and skills!</p>
  <a class="abs btn btn-blue" href="#">Discover More</a>
  <div class="abs arrows">
    <span class="arrow"><svg width="10" height="10" viewBox="0 0 10 10" fill="none" stroke="#fff" stroke-width="1.5"><path d="M6.5 1.5L3 5l3.5 3.5"/></svg></span>
    <span class="arrow"><svg width="10" height="10" viewBox="0 0 10 10" fill="none" stroke="#fff" stroke-width="1.5"><path d="M3.5 1.5L7 5 3.5 8.5"/></svg></span>
  </div>
  <div class="abs dots"><span></span><span></span><span></span></div>
</section>

<section class="abs about">
  <div class="abs photo photo-main" role="img" aria-label="Hand holding an endoscope control section"></div>
  <div class="abs photo photo-small" role="img" aria-label="Endoscope control body lying on a white surface"></div>
  <div class="abs badge"><svg width="50" height="50" viewBox="0 0 50 50" fill="none" stroke="#0aa1e2" stroke-width="2"><circle cx="25" cy="25" r="20"/><circle cx="25" cy="25" r="8"/></svg></div>
  <h2 class="abs">Endoscope repairs and second hand endoscopes from Lumavex – cause the outcome matters!</h2>
  <div class="abs copy">
    <p>Lumavex is a privileged partner for the start-up facility or optimisation of existing healthcare facilities, doctor's offices and hospitals. The quality and reliability of our products and our offered service are our best advertisement!</p>
    <p>As a result of optimised processes and highly qualified specialists in our company, we can work very quickly and with high quality for your benefit of least possible restrictions in your doctor's office or in your hospital.</p>
  </div>
  <ul class="abs checks">
    <li><span class="tick"><svg width="8" height="8" viewBox="0 0 8 8" fill="none" stroke="#fff" stroke-width="1.6"><path d="M1 4l2 2 4-4"/></svg></span>One company for everyone</li>
    <li><span class="tick"><svg width="8" height="8" viewBox="0 0 8 8" fill="none" stroke="#fff" stroke-width="1.6"><path d="M1 4l2 2 4-4"/></svg></span>Experience Charactersises Us</li>
    <li><span class="tick"><svg width="8" height="8" viewBox="0 0 8 8" fill="none" stroke="#fff" stroke-width="1.6"><path d="M1 4l2 2 4-4"/></svg></span>Guaranteed Service</li>
    <li><span class="tick"><svg width="8" height="8" viewBox="0 0 8 8" fill="none" stroke="#fff" stroke-width="1.6"><path d="M1 4l2 2 4-4"/></svg></span>Quality Not Quantity</li>
  </ul>
  <a class="abs btn btn-blue" href="#">Learn More</a>
</section>

<section class="abs brands">
  <span class="abs brand-name" style="left:331px">OLVARIN</span>
  <span class="abs brand-name" style="left:585px">PENTREL</span>
  <span class="abs brand-name" style="left:841px">FUJARIS</span>
</section>

<section class="abs services">
  <div class="abs eyebrow-dark">OUR SERVICES</div>
  <h2 class="abs">What We Do</h2>
  <article class="abs card" style="left:99px">
    <div class="pic" role="img" aria-label="Gloved hands servicing an endoscope" style="background:linear-gradient(135deg,#e9eef2,#a9c8de)"></div>
    <h3>Endoscope<br>Repair Service</h3>
    <p>Manufacturer-independent we repair and maintain endoscopes, individual components (e.g. processors or light sources), accessories and peripherals of the manufacturers Olvarin, Pentrel and Fujaris.</p>
    <a class="btn btn-blue" href="#">REPAIR REQUEST</a>
  </article>
  <article class="abs card" style="left:443px">
    <div class="pic" role="img" aria-label="Medical endoscopy equipment on a trolley" style="background:linear-gradient(135deg,#5d7fa3,#c9d8e6)"></div>
    <h3>Sale Used<br>Endoscopes</h3>
    <p>Manufacturer-independent we repair and maintain endoscopes, individual components (e.g. processors or light sources), accessories and peripherals of the manufacturers Olvarin, Pentrel and Fujaris.</p>
    <a class="btn btn-blue" href="#">REPAIR REQUEST</a>
  </article>
  <article class="abs card" style="left:785px">
    <div class="pic" role="img" aria-label="Coiled endoscope in a cleaning unit" style="background:linear-gradient(135deg,#3f86c6,#d9ebf7)"></div>
    <h3>Purchase Used<br>Endoscopes</h3>
    <p>Manufacturer-independent we repair and maintain endoscopes, individual components (e.g. processors or light sources), accessories and peripherals of the manufacturers Olvarin, Pentrel and Fujaris.</p>
    <a class="btn btn-blue" href="#">REPAIR REQUEST</a>
  </article>
</section>

<section class="abs faulty" role="img" aria-label="Technician working on an endoscope, tinted blue"></section>
<div class="abs trust">
  <svg class="ring" width="70" height="70" viewBox="0 0 70 70" fill="none" stroke="#fff" stroke-width="2.2"><circle cx="32" cy="32" r="26"/><circle cx="32" cy="32" r="10"/><path d="M50 50l14 14"/></svg>
  <p>We are trusted by<br>more than 250 Clients</p>
</div>
<div class="abs faulty-text">
  <h2>Faulty<br>Endoscope ?</h2>
  <p>We ensure quick and smooth repairs!</p>
</div>
<a class="abs btn btn-orange" href="#">PICK-UP ORDER</a>

<section class="abs decision">
  <h2 class="abs">Lumavex GmbH,<br>your decision for your future</h2>
  <div class="abs feature" style="left:267px;top:283px">
    <svg width="48" height="48" viewBox="0 0 48 48" fill="none" stroke="#0aa1e2" stroke-width="2.2"><circle cx="24" cy="24" r="20"/><path d="M24 12v12l8 6"/></svg>
    <h4>Fast repairs</h4>
    <p>Keep potential disruptions in your doctor's office or in your hospital at minimum as a result of optimized processes and highly qualified specialists in our company</p>
  </div>
  <div class="abs feature" style="left:615px;top:283px">
    <svg width="48" height="48" viewBox="0 0 48 48" fill="none" stroke="#0aa1e2" stroke-width="2.2"><path d="M6 22L24 6l18 16v20H30V30H18v12H6z"/></svg>
    <h4>On-site service</h4>
    <p>We will gladly pay you a visit to carry out analysis and repairs on site. Due to our many years of experience – it doesn't get any faster (within a 250 km range)</p>
  </div>
  <div class="abs feature" style="left:978px;top:283px">
    <svg width="48" height="48" viewBox="0 0 48 48" fill="none" stroke="#0aa1e2" stroke-width="2.2"><path d="M42 20A19 19 0 1134 9"/><path d="M15 23l8 8 20-21"/></svg>
    <h4>Without a maintenance<br>contract</h4>
    <p>No subscription or other maintenance contract, but one-time and sustainable repair work</p>
  </div>
  <div class="abs feature" style="left:267px;top:532px">
    <svg width="48" height="48" viewBox="0 0 48 48" fill="none" stroke="#0aa1e2" stroke-width="2.2"><path d="M12 4h18l8 8v32H12z"/><path d="M30 4v8h8"/><path d="M28 22h-5a3 3 0 000 6h3a3 3 0 010 6h-6M25 19v3M25 34v3"/></svg>
    <h4>Highly cost efficient</h4>
    <p>Benefit from our first class recommendations and implementation by our experienced staff. Our goals is to find the best solutions together with you at the best lowest price point.</p>
  </div>
  <div class="abs feature" style="left:615px;top:524px">
    <svg width="48" height="48" viewBox="0 0 48 48" fill="none" stroke="#0aa1e2" stroke-width="2.2"><rect x="4" y="10" width="40" height="28" rx="2"/><path d="M4 18h40M24 30l4 4 8-8"/></svg>
    <h4>Loan equipment service</h4>
    <p>Use our service of high-quality loan devices during the downtime of your defective endoscope (limited to stock)</p>
  </div>
  <div class="abs feature" style="left:978px;top:524px">
    <svg width="48" height="48" viewBox="0 0 48 48" fill="none" stroke="#0aa1e2" stroke-width="2.2"><path d="M4 22h9v22H4zM13 24l9-18c4 0 5 3 4 7l-2 7h16a4 4 0 014 5l-4 15a4 4 0 01-4 3H13"/></svg>
    <h4>First class service</h4>
    <p>Our clients always come first!</p>
  </div>
  <a class="abs btn btn-blue" href="#">MORE ABOUT US</a>
</section>

<section class="abs cta-band">
  <div class="abs label">DON'T HESITATE TO CONTACT US</div>
  <h2 class="abs">How Can We Help You ?</h2>
  <div class="abs sub">Let's get started now</div>
  <a class="abs btn" href="#">Discover More</a>
</section>

<footer class="abs footer">
  <div class="abs brand"><span class="mark"></span>Lumavex</div>
  <div class="abs col-about">
    <h5>About</h5>
    <ul><li>INFORMATIONS</li><li>ABOUT US</li><li>CONTACT US</li><li>TOS</li><li>COPYRIGHTS</li><li>PRIVACY POLICY</li></ul>
  </div>
  <div class="abs col-explore">
    <h5>Explore</h5>
    <ul><li>ENDOSCOPE REPAIR</li><li>USED ENDOSCOPES</li><li>ENDOSCOPY SYSTEMS</li><li>ENDOSCOPY ACCESSORIES</li><li>ACCESSORIES CATALOG</li><li>PURCHASE</li></ul>
  </div>
  <div class="abs contact-chip f-email">
    <span class="chip-icon"><svg width="18" height="14" viewBox="0 0 18 14" fill="none" stroke="#0aa1e2" stroke-width="1.5"><rect x="1" y="1" width="16" height="12" rx="1"/><path d="M1 2l8 6 8-6"/></svg></span>
    <div><div class="chip-label">EMAIL</div><div class="chip-value">info@lumavex.de</div></div>
  </div>
  <div class="abs contact-chip f-phone">
    <span class="chip-icon"><svg width="16" height="16" viewBox="0 0 24 24" fill="none" stroke="#0aa1e2" stroke-width="1.8"><path d="M5 3h4l2 5-2.5 1.5a11 11 0 006 6L16 13l5 2v4a2 2 0 01-2 2A16 16 0 013 5a2 2 0 012-2z"/></svg></span>
    <div><div class="chip-label">PHONE</div><div class="chip-value">+49 4151 555 720-0</div></div>
  </div>
  <div class="abs f-social"><span class="dot-icon"></span><span class="dot-icon"></span><span class="dot-icon"></span><span class="dot-icon"></span></div>
  <div class="abs rule"></div>
  <div class="abs copy">© Copyright 2022 by lumavex</div>
</footer>

</body>
</html>
```